KVM Contracting services . Building and maintenance services, optic fibre installation

Business cards and logo design.I need a logo that I can use on business cards ,workwear and on my vehicles. I would like the KVM to be the main or larger text and contracting services to be the smaller or less important text.I like monograms, modern designs and repeating patterns symbols. I am also a Gemini and my favourite number is 22 so if this can be any inspiration to help with the design. Am thinking of the using German flag colours as a his is my family’s heritage. And the other 2 main colours I wear is black and white.But any ideas are appreciated.I do not need a design that is trade specific but a design that could be used for any business.

Target Market(s)

General public

Contact Information for Business Card

KVM Contracting Services ( front of business card)

(Back of business card)
Darren Holtwick
0451907326
Maintenance services
Optic fibre and data installation

Logo Text

Logo can just be pattern or monogram or incorporate KVM . I like the gemini star sign and the number 22

Colors
ec1f27
000000
fbee3e
ffffff

Requirements
Must have
• Logo and KVM Contracting Services on the front of business card
Nice to have
• Possible use of German flag colours.
• Modern design.
• Design to be able to be used on black or white background as I want to put it on clothing

```html
<!DOCTYPE html>
<html lang="en">
<head>
<meta charset="utf-8">
<title>KVM Contracting Services – Business Cards</title>
<link rel="stylesheet" href="https://fonts.googleapis.com/css2?family=Mulish:wght@700;800&family=Open+Sans:wght@400&display=swap">
<style>
  :root {
    --backdrop: #7b7b7b;
    --card-light: #eeeeee;
    --card-dark: #141414;
    --ink: #111111;
    --paper: #ffffff;
    --brand-red: #ec1f27;
    --rule: #9a9a9a;
  }
  * { margin: 0; padding: 0; box-sizing: border-box; }
  html, body {
    width: 1200px;
    height: 1200px;
    overflow: hidden;
    background: var(--backdrop);
  }
  .stage { position: relative; width: 1200px; height: 1200px; }
  .card {
    position: absolute;
    top: 310px;
    height: 594px;
    text-align: center;
    box-shadow: 0 2px 6px rgba(0,0,0,0.35);
  }
  .card--back { left: 234px; width: 364px; background: var(--card-light); color: var(--ink); }
  .card--front { left: 627px; width: 370px; background: var(--card-dark); color: var(--paper); }

  .brand { position: absolute; left: 0; right: 0; }
  .card--back .brand { top: 150px; }
  .card--front .brand { top: 240px; }
  .brand__name {
    font-family: "Mulish", sans-serif;
    font-weight: 800;
    font-size: 92px;
    line-height: 86px;
    letter-spacing: 2px;
    color: var(--brand-red);
  }
  .brand__tagline {
    font-family: "Mulish", sans-serif;
    font-weight: 800;
    font-size: 21px;
    letter-spacing: 0.6px;
    margin-top: 2px;
  }

  .contact { position: absolute; left: 0; right: 0; top: 402px; }
  .contact__name {
    font-family: "Mulish", sans-serif;
    font-weight: 800;
    font-size: 23px;
    letter-spacing: 0.3px;
  }
  .contact__phone {
    font-family: "Open Sans", sans-serif;
    font-size: 21px;
    margin-top: 2px;
  }
  .contact__rule {
    width: 204px;
    height: 1px;
    background: var(--rule);
    margin: 12px auto 20px;
  }
  .contact__services {
    font-family: "Open Sans", sans-serif;
    font-size: 17px;
    line-height: 21px;
  }
</style>
</head>
<body>
  <main class="stage">
    <section class="card card--back" aria-label="Business card back">
      <div class="brand">
        <div class="brand__name">KVM</div>
        <div class="brand__tagline">CONTRACTING SERVICES</div>
      </div>
      <div class="contact">
        <div class="contact__name">DARREN HOLTWICK</div>
        <div class="contact__phone">0451907326</div>
        <div class="contact__rule"></div>
        <div class="contact__services">Maintenance services<br>Optic fibre and data installation</div>
      </div>
    </section>

    <section class="card card--front" aria-label="Business card front">
      <div class="brand">
        <div class="brand__name">KVM</div>
        <div class="brand__tagline">CONTRACTING SERVICES</div>
      </div>
    </section>
  </main>
</body>
</html>
```